Business Card Design

We need a business card designed for our new company. Prefer a black card with white logo & writing.

Contact Information for Business Card

Ted Galloway, address: 7-4812 Fernhollow Road, Abbotsford, BC, V3K 8R2, Office Phone: 604-712-3390, Cell: 604-947-2164, Email: ted@resinworkshub.ca

Colors

Designer to choose only greyscale colors for use in the design.

```html
<!DOCTYPE html>
<html lang="en">
<head>
<meta charset="utf-8">
<title>Resinworks Hub – Business Card</title>
<link rel="stylesheet" href="https://fonts.googleapis.com/css2?family=Montserrat:wght@400;500;700&display=swap">
<style>
  :root {
    --backdrop: #9a9a9a;
    --card-light: #ffffff;
    --card-dark: #222222;
    --ink: #111111;
    --ink-soft: #1d1d1d;
    --paper-text: #ffffff;
  }
  * { margin: 0; padding: 0; box-sizing: border-box; }
  html, body {
    width: 1093px;
    height: 1200px;
    overflow: hidden;
    background: var(--backdrop);
    font-family: "Montserrat", Arial, sans-serif;
  }
  .canvas { position: relative; width: 1093px; height: 1200px; }

  .card {
    position: absolute;
    left: 264px;
    width: 581px;
    border-radius: 15px;
    overflow: hidden;
  }
  .card--front { top: 225px; height: 363px; background: var(--card-light); color: var(--ink); }
  .card--back { top: 616px; height: 366px; background: var(--card-dark); color: var(--paper-text); }

  .holder { position: absolute; left: 29px; top: 42px; }
  .holder__name { font-size: 21px; font-weight: 700; letter-spacing: 0.2px; line-height: 1; }
  .holder__role { font-size: 13px; font-weight: 400; margin-top: 8px; }

  .brand {
    display: flex;
    align-items: center;
    gap: 7px;
    font-weight: 700;
    white-space: nowrap;
  }
  .brand__dot { border-radius: 50%; background: currentColor; flex: none; }
  .brand--front { position: absolute; right: 26px; top: 64px; font-size: 19px; color: var(--ink); }
  .brand--front .brand__dot { width: 12px; height: 12px; }
  .brand--back {
    position: absolute; left: 50%; top: 50%;
    transform: translate(-50%, -50%);
    font-size: 36px; color: var(--paper-text); gap: 12px;
  }
  .brand--back .brand__dot { width: 22px; height: 22px; }

  .contacts { position: absolute; left: 28px; top: 255px; list-style: none; }
  .contacts__item {
    display: flex; align-items: center; gap: 9px;
    font-size: 13px; font-weight: 400; height: 22px; color: var(--ink-soft);
  }
  .contacts__icon { width: 13px; height: 13px; flex: none; fill: var(--ink); }

  .address {
    position: absolute; left: 387px; top: 309px;
    font-size: 13.5px; font-style: normal; line-height: 16px; color: var(--ink-soft);
  }
</style>
</head>
<body>
<main class="canvas">
  <section class="card card--front" aria-label="Business card front">
    <div class="holder">
      <h1 class="holder__name">Ted Galloway</h1>
      <p class="holder__role">owner</p>
    </div>

    <div class="brand brand--front"><span class="brand__dot"></span>Resinworks Hub</div>

    <ul class="contacts">
      <li class="contacts__item">
        <svg class="contacts__icon" viewBox="0 0 24 24" aria-hidden="true"><path d="M6.6 10.8a15.1 15.1 0 0 0 6.6 6.6l2.2-2.2a1 1 0 0 1 1-.25 11.4 11.4 0 0 0 3.6.57 1 1 0 0 1 1 1V20a1 1 0 0 1-1 1A17 17 0 0 1 3 4a1 1 0 0 1 1-1h3.5a1 1 0 0 1 1 1c0 1.25.2 2.45.57 3.57a1 1 0 0 1-.25 1z"/></svg>
        604-712-3390
      </li>
      <li class="contacts__item">
        <svg class="contacts__icon" viewBox="0 0 24 24" aria-hidden="true"><path d="M7 1h10a2 2 0 0 1 2 2v18a2 2 0 0 1-2 2H7a2 2 0 0 1-2-2V3a2 2 0 0 1 2-2zm0 3v14h10V4zm5 15.5a1.2 1.2 0 1 0 0 2.4 1.2 1.2 0 0 0 0-2.4z"/></svg>
        604-947-2164
      </li>
      <li class="contacts__item">
        <svg class="contacts__icon" viewBox="0 0 24 24" aria-hidden="true"><path d="M2 5h20v2l-10 6L2 7zm0 4.3 10 6 10-6V19H2z"/></svg>
        ted@resinworkshub.ca
      </li>
      <li class="contacts__item">
        <svg class="contacts__icon" viewBox="0 0 24 24" aria-hidden="true"><path d="M12 2a10 10 0 1 0 0 20 10 10 0 0 0 0-20zm-1 17.9A8 8 0 0 1 4.2 10L9 14.8v1a2 2 0 0 0 2 2zm6.9-2.5A2 2 0 0 0 16 16h-1v-3a1 1 0 0 0-1-1H8v-2h2a1 1 0 0 0 1-1V7h2a2 2 0 0 0 2-2v-.4a8 8 0 0 1 2.9 12.8z"/></svg>
        www.resinworkshub.ca
      </li>
    </ul>

    <address class="address">7-4812 Fernhollow Road,<br>Abbotsford, BC, V3K 8R2</address>
  </section>

  <section class="card card--back" aria-label="Business card back">
    <div class="brand brand--back"><span class="brand__dot"></span>Resinworks Hub</div>
  </section>
</main>
</body>
</html>
```